Upmarket Dessert Lounge needs a Business Card Design

We are an upmarket dessert lounge needing a business card to match our image.

We want something that is simple yet beautiful, feminine, classy, sophisticated and elegant. We want it to stand out and don't mind if it is bold.

The design should include our logo and colours of red or maroon with gold highlights. We don't mind if black is used.

Marlow & Quince

Target Market(s)

For those who like to indulge or treat themselves and give in to their temptations on good quality desserts.

Industry/Entity Type

Business

Requirements
Must have
• Must include our logo and our name

Marlow & Quince

M & Q

```html
<!DOCTYPE html>
<html lang="en">
<head>
<meta charset="utf-8">
<title>Marlow &amp; Quince — Business Card</title>
<link rel="stylesheet" href="https://fonts.googleapis.com/css2?family=Open+Sans:wght@400;600&display=swap">
<style>
  :root {
    --backdrop: #e9e6e2;
    --card: #ffffff;
    --maroon: #7a1f1c;
    --maroon-dark: #5a1210;
    --maroon-light: #a8322b;
    --gold: #e9c89a;
    --gold-light: #f6dfbd;
    --ink: #2a2a2a;
  }
  * { box-sizing: border-box; margin: 0; padding: 0; }
  html, body { width: 1200px; height: 951px; overflow: hidden; }
  body {
    background: var(--backdrop);
    font-family: "Open Sans", sans-serif;
    color: var(--ink);
    position: relative;
  }
  .card {
    position: absolute;
    background: var(--card);
    border-radius: 26px;
    overflow: hidden;
    box-shadow: 0 10px 28px rgba(0,0,0,0.18);
  }
  .card-front { left: 90px; top: 50px; width: 640px; height: 380px; }
  .card-back { left: 470px; top: 480px; width: 660px; height: 390px; }

  .wordmark {
    color: var(--maroon);
    font-weight: 400;
    text-transform: uppercase;
    white-space: nowrap;
    display: flex;
    align-items: center;
  }
  .wordmark-dot {
    background: var(--maroon);
    border-radius: 50%;
    flex: none;
  }
  .card-front .wordmark {
    position: absolute;
    left: 0; right: 0; top: 150px;
    justify-content: center;
    font-size: 40px;
    letter-spacing: 6px;
    gap: 22px;
  }
  .card-front .wordmark-dot { width: 16px; height: 16px; }
  .card-front .web {
    position: absolute;
    left: 0; right: 0; top: 296px;
    text-align: center;
    font-size: 20px;
    letter-spacing: 2px;
  }

  .card-back .wordmark {
    position: absolute;
    left: 48px; top: 62px;
    font-size: 24px;
    letter-spacing: 3px;
    gap: 14px;
  }
  .card-back .wordmark-dot { width: 11px; height: 11px; }
  .card-back .business-name {
    position: absolute;
    right: 42px; top: 108px;
    font-size: 23px;
    color: var(--maroon);
    letter-spacing: 0.5px;
  }
  .contacts {
    position: absolute;
    left: 36px; top: 232px;
    list-style: none;
    font-size: 17px;
    line-height: 22px;
  }
  .contacts li { display: flex; align-items: center; gap: 9px; }
  .contacts svg { width: 14px; height: 14px; fill: var(--maroon); flex: none; }
  .address {
    position: absolute;
    left: 415px; top: 272px;
    display: flex; gap: 10px;
    font-size: 17px; line-height: 22px;
    font-style: normal;
  }
  .address svg { width: 15px; height: 15px; fill: var(--maroon); margin-top: 3px; flex: none; }
  .base-band { position: absolute; left: 0; bottom: 0; width: 660px; height: 60px; }
</style>
</head>
<body>

<section class="card card-front" aria-label="Card front">
  <div class="wordmark"><span class="wordmark-dot"></span>Marlow &amp; Quince</div>
  <p class="web">www.marlowquince.com</p>
</section>

<section class="card card-back" aria-label="Card back">
  <div class="wordmark"><span class="wordmark-dot"></span>Marlow &amp; Quince</div>
  <p class="business-name">Marlow &amp; Quince</p>

  <ul class="contacts">
    <li><svg viewBox="0 0 16 16"><path d="M4 1l3 3-2 2c1 2 3 4 5 5l2-2 3 3-2 3C7 15 1 9 1 3z"/></svg>512-555-0148</li>
    <li><svg viewBox="0 0 16 16"><rect x="4" y="1" width="8" height="5"/><rect x="1" y="6" width="14" height="7" rx="1"/></svg>512-555-0149</li>
    <li><svg viewBox="0 0 16 16"><path d="M1 5l7 5 7-5v9H1z M1 3h14L8 8z"/></svg>info@marlowquince.com</li>
    <li><svg viewBox="0 0 16 16"><circle cx="8" cy="8" r="7"/></svg>www.marlowquince.com</li>
  </ul>

  <address class="address">
    <svg viewBox="0 0 16 16"><path d="M8 1l7 7h-2v7H9v-4H7v4H3V8H1z"/></svg>
    <span>418 Linden Row<br>Suite 210-045<br>Harlow, TX 78114</span>
  </address>

  <svg class="base-band" viewBox="0 0 660 60" preserveAspectRatio="none" aria-hidden="true">
    <defs>
      <linearGradient id="bandMaroon" x1="0" y1="0" x2="0" y2="1">
        <stop offset="0" stop-color="#a8322b"/>
        <stop offset="1" stop-color="#5a1210"/>
      </linearGradient>
      <linearGradient id="bandGold" x1="0" y1="0" x2="1" y2="0">
        <stop offset="0" stop-color="#e9c89a"/>
        <stop offset="1" stop-color="#f6dfbd"/>
      </linearGradient>
    </defs>
    <path d="M0 20 L440 34 L470 60 L0 60 Z" fill="url(#bandMaroon)"/>
    <path d="M460 38 L660 34 L660 60 L485 60 Z" fill="url(#bandGold)"/>
  </svg>
</section>

</body>
</html>
```